Business card for a Exhibition booth fabrication company

Hi. My company would like to change our corporate name card. We are an events and Exhibition stand builder company. We would like our corporate name card to resonate what we do. I need someone to create something unique that relates to the industry that I am in. The graphic designer should be creative to incorporate the elements of my industry and try to blend in well in the design of the card. Our aim is to ensure that we are unique and our card can look different from our competitors.
Updates

Target Market(s)

Marketing and events manager from all companies

Contact Information for Business Card

The business card should have the following details:
Name
Job Title
Email
Website

Colors

Designer to choose colors to be used in the design.

Requirements
Must have
• The card must be look something that is relevant to the service that I am providing. My website is: www.velmora-buildworks.com
• You can see my website to get more information on what service that I am doing
Nice to have
• On the back of my card, I would like to have a globe image with the incorporation of my company logo. This is to indicate that my services can be done in any part of the world.

```html
<!DOCTYPE html>
<html lang="en">
<head>
<meta charset="utf-8">
<title>Velmora Buildworks — Business Card</title>
<link href="https://fonts.googleapis.com/css2?family=Arimo:wght@700&family=Open+Sans:wght@400;600&display=swap" rel="stylesheet">
<style>
  :root {
    --bg-light: #dcdddf;
    --bg-dark: #a4a5a8;
    --card: #ffffff;
    --card-edge: #b9babc;
    --brand-red: #e3202a;
    --ink: #58595b;
    --ink-soft: #6d6e71;
    --rule: #c7c8ca;
    --map-light: #ececed;
    --map-dark: #bdbec0;
  }
  * { margin: 0; padding: 0; box-sizing: border-box; }
  html, body { width: 1200px; height: 1118px; overflow: hidden; }
  body {
    position: relative;
    background: linear-gradient(90deg, var(--bg-light) 0%, #c3c4c6 55%, var(--bg-dark) 100%);
    font-family: "Open Sans", Arial, sans-serif;
    color: var(--ink);
  }
  .card {
    position: absolute;
    left: 222px;
    width: 756px;
    background: var(--card);
    border: 1px solid var(--card-edge);
    border-radius: 46px;
    overflow: hidden;
  }
  .card--front { top: 88px; height: 431px; }
  .card--back { top: 579px; height: 431px; }

  /* Front */
  .brand {
    position: absolute;
    left: 0; width: 414px;
    top: 180px;
    display: flex; align-items: center; justify-content: center; gap: 12px;
  }
  .brand__mark { width: 18px; height: 18px; background: var(--brand-red); }
  .brand__name {
    font-weight: 600; font-size: 22px; letter-spacing: 2px;
    color: var(--ink-soft);
  }
  .divider {
    position: absolute; left: 406px; top: 105px;
    width: 2px; height: 225px; background: var(--rule);
  }
  .details { position: absolute; left: 425px; top: 96px; }
  .details__name {
    font-family: "Arimo", Arial, sans-serif; font-weight: 700;
    font-size: 27px; letter-spacing: 0.5px; color: var(--brand-red);
    line-height: 34px;
  }
  .details__title { font-size: 20px; line-height: 28px; letter-spacing: 0.5px; color: var(--ink-soft); }
  .details__address { margin-top: 16px; font-size: 18px; line-height: 25px; color: var(--ink); }
  .contacts { list-style: none; margin-top: 15px; }
  .contacts__item {
    display: flex; align-items: center; gap: 12px;
    font-size: 18px; line-height: 35px; color: var(--ink);
  }
  .contacts__icon { width: 20px; height: 20px; flex: none; fill: var(--brand-red); }

  /* Back */
  .world-map {
    position: absolute; left: 45px; top: 50px; width: 672px; height: 282px;
    border-radius: 50% 50% 18% 18% / 75% 75% 20% 20%;
    background: radial-gradient(ellipse at 50% 30%, var(--map-dark) 0%, #d3d4d6 45%, var(--map-light) 75%, rgba(255,255,255,0) 100%);
    opacity: 0.8;
  }
  .ground-shadow {
    position: absolute; left: 70px; top: 340px; width: 620px; height: 38px;
    border-radius: 50%;
    background: radial-gradient(ellipse at center, rgba(0,0,0,0.13) 0%, rgba(0,0,0,0) 70%);
  }
  .back-brand {
    position: absolute; left: 0; width: 100%; top: 258px;
    text-align: center;
    font-weight: 600; font-size: 30px; letter-spacing: 2px; color: var(--brand-red);
  }
  .back-web {
    position: absolute; left: 0; width: 100%; top: 390px;
    text-align: center; font-size: 22px; letter-spacing: 4.5px; color: #231f20;
  }
</style>
</head>
<body>
  <section class="card card--front">
    <div class="brand">
      <span class="brand__mark"></span>
      <span class="brand__name">VELMORA BUILDWORKS</span>
    </div>
    <div class="divider"></div>
    <div class="details">
      <p class="details__name">DANIEL HARWICK</p>
      <p class="details__title">PRESIDENT</p>
      <p class="details__address">Street Name, City Name<br>Zipcode - 01234</p>
      <ul class="contacts">
        <li class="contacts__item">
          <svg class="contacts__icon" viewBox="0 0 24 24"><path d="M6.6 10.8c1.4 2.8 3.8 5.1 6.6 6.6l2.2-2.2c.3-.3.7-.4 1-.2 1.1.4 2.3.6 3.6.6.6 0 1 .4 1 1V20c0 .6-.4 1-1 1C10.6 21 3 13.4 3 4c0-.6.4-1 1-1h3.5c.6 0 1 .4 1 1 0 1.3.2 2.5.6 3.6.1.3 0 .7-.2 1L6.6 10.8z"/></svg>
          <span>012-345-6789</span>
        </li>
        <li class="contacts__item">
          <svg class="contacts__icon" viewBox="0 0 24 24"><path d="M2 5h20v14H2z M3.5 6.5 12 12.5l8.5-6" fill="none" stroke="#e3202a" stroke-width="0"/><path d="M2 5h20v2l-10 6.5L2 7z"/><path d="M2 9l10 6.5L22 9v10H2z"/></svg>
          <span>info@velmora-buildworks.com</span>
        </li>
        <li class="contacts__item">
          <svg class="contacts__icon" viewBox="0 0 24 24" fill="none" stroke="#e3202a" stroke-width="1.8"><circle cx="12" cy="12" r="9"/><ellipse cx="12" cy="12" rx="4" ry="9"/><path d="M3 12h18M4.5 7.5h15M4.5 16.5h15"/></svg>
          <span>www.velmora-buildworks.com</span>
        </li>
      </ul>
    </div>
  </section>

  <section class="card card--back">
    <div class="world-map" role="img" aria-label="Light grey world map spread across a curved globe surface"></div>
    <div class="ground-shadow"></div>
    <p class="back-brand">VELMORA BUILDWORKS</p>
    <p class="back-web">www.velmora-buildworks.com</p>
  </section>
</body>
</html>
```